Hybrid Seed corn and Soybean Sales business needs a website.

We here at "KW Grain" feel that we need a website to show a very professional side to our customer base. Although no actual ordering will take place on this website, we would like to put Plot and field trail data on the website. Along with a brief page for each of our hybrids and a place for customers to sign up for a newsletter. The company we sell hybrids for is MolvanGrain.com... Im not sure how this process works as far as myself updating the information or having the data actually put on the website, but feel free to contact me if you need the information. I will attach the logo for the company, (KW Grain).

Target Market(s)

Farmers, "Producers", Corn and soybean production

Industry/Entity Type

Business

Coding

Coded - Design and coding required

Number of Pages Required

5+ page

Colors
f78f20
ffffff

Requirements
Nice to have
• Similar layout to http://www.molvangrain.com/
• And it would be nice to incorporate our story into the website
• http://www.molvangrain.com/our-story/molvan-today/

```html
<!DOCTYPE html>
<html lang="en">
<head>
<meta charset="utf-8">
<title>KW Grain – Hybrid Seeds of Corn &amp; Soybean</title>
<link href="https://fonts.googleapis.com/css2?family=Ubuntu:wght@400;500;700&display=swap" rel="stylesheet">
<style>
:root{
  --orange:#ea870c;
  --orange-bright:#f78f20;
  --orange-btn:#ef8a12;
  --green:#6aab1e;
  --white:#ffffff;
  --ink:#555555;
  --rule:#e4e4e4;
}
*{box-sizing:border-box;margin:0;padding:0}
html,body{width:1000px;height:1200px;overflow:hidden}
body{background:var(--orange);font-family:"Ubuntu",sans-serif;color:var(--ink);position:relative}
a{text-decoration:none;color:inherit}
.abs{position:absolute}
.page{position:absolute;left:97px;top:52px;width:806px;height:1056px;background:var(--white)}

/* header */
.brand{left:10px;top:24px;display:flex;align-items:center;gap:6px;font-weight:700;font-size:17px;color:var(--orange-bright);letter-spacing:.5px}
.brand-dot{width:14px;height:14px;border-radius:50%;background:var(--green)}
.nav-link{top:0;height:80px;line-height:80px;font-size:11.5px;font-weight:500;color:#555;white-space:nowrap}
.nav-link.active{left:298px;width:63px;text-align:center;background:linear-gradient(#f4a20c,#e8760a);color:var(--white)}
.search{left:759px;top:27px;width:33px;height:33px;border-radius:50%;background:var(--green);display:flex;align-items:center;justify-content:center}

/* hero */
.hero{left:10px;top:80px;width:786px;height:386px;background:
  radial-gradient(ellipse at 70% 35%,#b0733a 0%,transparent 45%),
  radial-gradient(ellipse at 15% 30%,#e0700e 0%,transparent 40%),
  linear-gradient(180deg,#c0601a 0%,#e67818 55%,#d45a10 100%)}
.hero-caption{left:68px;top:134px;width:342px;height:146px;background:rgba(40,30,20,.55)}
.hero-caption h1{position:absolute;left:18px;top:14px;font-weight:500;font-size:30px;line-height:31px;color:var(--white);letter-spacing:-1px;white-space:nowrap}
.btn-green{position:absolute;left:22px;top:90px;width:102px;height:34px;line-height:34px;text-align:center;background:var(--green);color:var(--white);font-size:11.5px;font-weight:500}
.hero-arrow{top:173px;width:33px;height:33px;border-radius:50%;background:var(--white);display:flex;align-items:center;justify-content:center}

/* about */
.section-title{font-size:20px;font-weight:500;color:#555;letter-spacing:-.5px}
.video{left:10px;top:531px;width:248px;height:132px;background:radial-gradient(ellipse at 30% 45%,#f0a030 0%,#a04a10 35%,#2a1a10 80%)}
.play{left:106px;top:49px;width:35px;height:35px;border-radius:50%;background:var(--white);display:flex;align-items:center;justify-content:center}
.about-copy{left:268px;top:528px;width:262px;font-size:8.8px;line-height:16.6px;color:#444;letter-spacing:-.25px}
.about-copy p+p{margin-top:8px}

/* newsletter */
.newsletter{left:548px;top:488px;width:248px;height:181px;background:linear-gradient(150deg,#8cc63f 0%,#5a9a16 100%);color:var(--white)}
.newsletter h2{position:absolute;left:15px;top:10px;font-size:19.5px;font-weight:500;letter-spacing:-.6px;white-space:nowrap}
.newsletter p{position:absolute;left:15px;top:48px;width:220px;font-size:8.6px;line-height:16.5px;letter-spacing:-.2px}
.field{position:absolute;left:14px;width:220px;height:20px;line-height:20px;background:rgba(70,110,10,.55);font-size:7.5px;padding:0 7px;color:#dfeecb}
.btn-orange{display:inline-block;background:var(--orange-btn);color:var(--white);font-size:10.5px;font-weight:500;height:21px;line-height:21px;padding:0 9px}
.newsletter .btn-orange{position:absolute;left:14px;top:139px}

/* comparison */
.compare{top:702px;width:383px;height:195px;padding:47px 26px}
.compare.corn{left:10px;background:linear-gradient(135deg,#8a5a22 0%,#c89a3c 45%,#e0b860 60%,#6a4a20 100%)}
.compare.soy{left:414px;background:linear-gradient(180deg,#8cc2e8 0%,#6cae2c 18%,#3e8a12 60%,#1f5a08 100%)}
.compare h3{font-size:24px;font-weight:500;line-height:29px;color:var(--white);letter-spacing:-.6px;text-shadow:0 1px 2px rgba(0,0,0,.4);white-space:nowrap}
.compare .btn-orange{margin-top:14px}

/* partners */
.partners-title{left:0;top:939px;width:806px;text-align:center}
.partners-rule{left:10px;top:974px;width:786px;height:1px;background:var(--rule)}
.partner{top:997px;height:30px;display:flex;align-items:center;gap:8px;font-weight:700;font-size:24px;color:#333}
.partner .mark{width:16px;height:16px;background:#888}

/* footer */
.footer-nav{left:97px;top:1134px;font-size:11px;font-weight:500;color:var(--white);display:flex;white-space:nowrap}
.footer-nav span{margin:0 15px}
.copyright{left:97px;top:1160px;font-size:10.5px;font-weight:500;color:var(--white)}
.social{top:1134px;width:30px;height:30px;border-radius:50%;color:var(--white);font-size:7px;display:flex;align-items:center;justify-content:center}
</style>
</head>
<body>
<div class="page">
  <header>
    <a class="abs brand" href="#"><span class="brand-dot"></span>KW GRAIN</a>
    <nav>
      <a class="abs nav-link active" href="#">Home</a>
      <a class="abs nav-link" href="#" style="left:379px">About Us</a>
      <a class="abs nav-link" href="#" style="left:459px">Services</a>
      <a class="abs nav-link" href="#" style="left:535px">Events</a>
      <a class="abs nav-link" href="#" style="left:602px">Products</a>
      <a class="abs nav-link" href="#" style="left:681px">Contact Us</a>
    </nav>
    <a class="abs search" href="#" aria-label="Search">
      <svg width="13" height="13" viewBox="0 0 13 13"><circle cx="5.5" cy="5.5" r="4" fill="none" stroke="#fff" stroke-width="2"/><line x1="8.5" y1="8.5" x2="12" y2="12" stroke="#fff" stroke-width="2"/></svg>
    </a>
  </header>

  <section class="abs hero" role="img" aria-label="Corn cobs and a burlap sack spilling orange corn kernels on wood">
    <div class="abs hero-caption">
      <h1>We sell hybrid seeds of<br>Corn &amp; Soybean</h1>
      <a class="btn-green" href="#">Learn More</a>
    </div>
    <span class="abs hero-arrow" style="left:14px">
      <svg width="14" height="14" viewBox="0 0 14 14"><polyline points="9,2 4,7 9,12" fill="none" stroke="#444" stroke-width="2.5"/></svg>
    </span>
    <span class="abs hero-arrow" style="left:738px">
      <svg width="14" height="14" viewBox="0 0 14 14"><polyline points="5,2 10,7 5,12" fill="none" stroke="#444" stroke-width="2.5"/></svg>
    </span>
  </section>

  <h2 class="abs section-title" style="left:10px;top:498px">About Us</h2>
  <div class="abs video" role="img" aria-label="Video still of a sunset over a field">
    <span class="abs play"><svg width="14" height="14" viewBox="0 0 14 14"><polygon points="3,1 13,7 3,13" fill="#444"/></svg></span>
  </div>
  <div class="abs about-copy">
    <p>Lorem Ipsum is simply dummy text of the printing and typesetting industry. Lorem Ipsum has been the industry's standard dummy text ever since the 1500s, when an unknown printer took a galley of type and scrambled it to make a type specimen book. It has survived not only five centuries, but also the leap into electronic typesetting, remaining essentially unchanged.</p>
    <p>It was popularised in the 1960s with the release of Letraset sheets containing Lorem Ipsum passages.</p>
  </div>

  <aside class="abs newsletter">
    <h2>Sign Up For A Newsletter</h2>
    <p>Lorem Ipsum is simply dummy text of the printing and typesetting industry.</p>
    <span class="field" style="top:90px">Enter Your Name</span>
    <span class="field" style="top:113px">Enter Your E-Mail ID</span>
    <a class="btn-orange" href="#">Subscribe</a>
  </aside>

  <article class="abs compare corn" role="img" aria-label="Ripe corn cob in a field">
    <h3>Comparision<br>For hybrid Seeds Corn</h3>
    <a class="btn-orange" href="#">Compare Now</a>
  </article>
  <article class="abs compare soy" role="img" aria-label="Green soybean field under a blue sky">
    <h3>Comparision<br>For hybrid Seeds Soyabeans</h3>
    <a class="btn-orange" href="#">Compare Now</a>
  </article>

  <h2 class="abs section-title partners-title">Our Partner Logo’s</h2>
  <div class="abs partners-rule"></div>
  <div class="abs partner" style="left:73px"><span class="mark"></span>Verdanta</div>
  <div class="abs partner" style="left:343px"><span class="mark"></span>Molvan</div>
  <div class="abs partner" style="left:560px;font-size:18px"><span class="mark"></span>Northfield Agro</div>
</div>

<footer>
  <nav class="abs footer-nav">
    <a href="#">Home</a><span>|</span><a href="#">About Us</a><span>|</span><a href="#">Services</a><span>|</span><a href="#">Events</a><span>|</span><a href="#">Products</a><span>|</span><a href="#">Contact Us</a>
  </nav>
  <p class="abs copyright">© 2015 Company Name , All Rights Reserved</p>
  <a class="abs social" href="#" style="left:837px;background:#2f4f8f">Follow</a>
  <a class="abs social" href="#" style="left:874px;background:#33a8d8">Feed</a>
</footer>
</body>
</html>
```